HearthMile business card and stationary design

We are looking for a simple yet elegant design for our mortgage company business card and stationary.

The card should include:
Name (Marcus Pell)
Title (CEO)
Phone Number (732-555-0182)
Address (48 Birchwell Court, Suite 314, Hazlet, NJ 07730)
Email (email@hearthmile.example)
"NMLS" i.e. (NMLS 61947)
"Company NMLS" (Company NMLS 274615)

Contact Information for Business Card

See above

```html
<!DOCTYPE html>
<html lang="en">
<head>
<meta charset="utf-8">
<title>HearthMile Business Card</title>
<link rel="stylesheet" href="https://fonts.googleapis.com/css2?family=Montserrat:wght@400;500;700;800&display=swap">
<style>
  :root {
    --bg: #15181c;
    --navy: #1b2430;
    --navy-light: #232f3d;
    --blue: #29a8e0;
    --white: #ffffff;
    --text: #e9eef3;
  }
  * { box-sizing: border-box; margin: 0; padding: 0; }
  html, body {
    width: 1200px; height: 900px; overflow: hidden;
    background: var(--bg);
    font-family: "Montserrat", Arial, sans-serif;
  }
  .stage {
    width: 1200px; height: 900px;
    display: flex; flex-direction: column;
    align-items: center; justify-content: center; gap: 60px;
  }
  .card {
    position: relative;
    width: 660px; height: 377px;
    border-radius: 26px;
    overflow: hidden;
    background: linear-gradient(160deg, var(--navy) 40%, var(--navy-light) 100%);
    box-shadow: 0 18px 40px rgba(0,0,0,.55);
  }
  /* Contact side */
  .card-contact .brand-panel {
    position: absolute; inset: 0;
    background: var(--white);
    clip-path: polygon(0 0, 46% 0, 28% 100%, 0 100%);
  }
  .card-contact .brand-vertical {
    position: absolute;
    left: 122px; top: 188px;
    transform: translate(-50%, -50%) rotate(-62deg);
    font-weight: 700; font-size: 46px; letter-spacing: .5px;
    color: var(--blue); white-space: nowrap;
  }
  .details {
    position: absolute; left: 318px; top: 62px;
    color: var(--text);
  }
  .details .name {
    font-weight: 800; font-size: 26px; color: var(--blue);
    text-transform: uppercase; letter-spacing: .5px;
  }
  .details .title {
    font-weight: 800; font-size: 15px; color: var(--white);
    margin-bottom: 18px;
  }
  .details .license { font-size: 14px; line-height: 1.55; }
  .contact-list { list-style: none; margin-top: 12px; font-size: 14px; line-height: 1.75; }
  .contact-list li { display: flex; align-items: center; gap: 10px; }
  .contact-list svg { width: 15px; height: 15px; flex: none; }
  .address { font-size: 14px; line-height: 1.55; margin-top: 10px; }
  /* Logo side */
  .card-logo { display: flex; align-items: center; justify-content: center; }
  .card-logo .brand-wordmark {
    font-weight: 700; font-size: 76px; letter-spacing: 1px;
    color: var(--blue);
  }
</style>
</head>
<body>
<main class="stage">
  <section class="card card-contact" aria-label="Business card, contact side">
    <div class="brand-panel"></div>
    <div class="brand-vertical">HearthMile</div>
    <div class="details">
      <p class="name">Marcus Pell</p>
      <p class="title">CEO</p>
      <p class="license">"NMLS" i.e. (NMLS 61947)<br>Company NMLS 274615</p>
      <ul class="contact-list">
        <li>
          <svg viewBox="0 0 16 16" aria-hidden="true"><circle cx="8" cy="8" r="8" fill="var(--blue)"/><path d="M5 4.2l1.6-.4.9 2.2-1 .8a5.5 5.5 0 0 0 2.7 2.7l.8-1 2.2.9-.4 1.6c-.2.4-.6.6-1 .6A7.3 7.3 0 0 1 4.4 5.2c0-.4.2-.8.6-1z" fill="var(--navy)"/></svg>
          732-555-0182
        </li>
        <li>
          <svg viewBox="0 0 16 16" aria-hidden="true"><rect x="1" y="3.5" width="14" height="9" rx="1" fill="var(--blue)"/><path d="M1.5 4l6.5 5 6.5-5" stroke="var(--navy)" stroke-width="1.2" fill="none"/></svg>
          email@hearthmile.example
        </li>
        <li>
          <svg viewBox="0 0 16 16" aria-hidden="true"><circle cx="8" cy="8" r="7" fill="var(--blue)"/><path d="M1 8h14M8 1c-3 3.5-3 10.5 0 14M8 1c3 3.5 3 10.5 0 14" stroke="var(--navy)" stroke-width="1" fill="none"/></svg>
          www.hearthmile.example
        </li>
      </ul>
      <p class="address">48 Birchwell Court, Suite<br>314, Fernhollow, NJ 08999</p>
    </div>
  </section>

  <section class="card card-logo" aria-label="Business card, brand side">
    <span class="brand-wordmark">HearthMile</span>
  </section>
</main>
</body>
</html>
```